Juice up my new website for book profits on Bravelmart

I have a website that needs a new look. I made a video of the past and in progress website: http://vextrola.com/qp8zkT2WMD.... here is the site in progress. http://brew.dormacrestclass.org/...this will be a WordPress website......https://snapvault.example/store/20180305134456/http://www.pressing-hints.com/

This website is setup to primary sell on Bravelmart.

eBook: https://www.bravelmart.com/Fresh-Blend-Dishes-For-Vigor-ebook/dp/K42RRQWMTX/ref=sr_1_4?dchild=1&keywords=Fresh+and+Blend+dishes+for+vigor&qid=1634055930&s=books&sr=1-4

Target Market(s)

Health and weight conscience people

Industry/Entity Type

Health

Number of Pages Required

2 page

Font styles to use
Serif

Requirements
Must have
• slider, sign up form, buy the ebook or hardcopy book.
Nice to have
• happy people drinking juice
Should not have
• Sidebar

```html
<!DOCTYPE html>
<html lang="en">
<head>
<meta charset="utf-8">
<title>Pressing Hints — Fresh and Blend Dishes For Vigor</title>
<link href="https://fonts.googleapis.com/css2?family=Oswald:wght@400;500&family=Poppins:wght@400;600;700&family=IBM+Plex+Serif:wght@400&family=Inter:wght@400;600&family=Montserrat:wght@400;500&display=swap" rel="stylesheet">
<style>
:root{
  --red:#e03a1e;
  --brand:#c41f2d;
  --ink:#1b1b1b;
  --muted:#444;
  --line:#d9d9d9;
  --blush:#f4efee;
  --dark:#231f1d;
  --white:#fff;
}
*{box-sizing:border-box;margin:0;padding:0}
html,body{width:1200px;height:3796px;overflow:hidden}
body{position:relative;background:var(--white);color:var(--ink);font-family:'Inter',sans-serif}
.abs{position:absolute}
.brand{font-family:'Poppins',sans-serif;font-weight:700;color:var(--brand);font-size:27px;letter-spacing:.5px;display:flex;align-items:center;gap:8px;text-transform:uppercase;white-space:nowrap}
.brand i{width:12px;height:12px;background:var(--brand);border-radius:50%;display:block}
.nav{font-family:'Poppins',sans-serif;font-size:14px;letter-spacing:.3px}
.nav a{color:var(--ink);text-decoration:none;position:absolute;white-space:nowrap}
.site-header{top:0;left:0;width:1200px;height:80px;background:var(--white);box-shadow:0 1px 0 #eee}
.hero{top:80px;left:0;width:1200px;height:557px;
  background:
    radial-gradient(ellipse 150px 190px at 845px 300px,rgba(244,168,30,.85),rgba(244,168,30,0) 70%),
    radial-gradient(ellipse 260px 330px at 880px 320px,rgba(120,80,55,.55),rgba(120,80,55,0) 75%),
    radial-gradient(ellipse 300px 260px at 960px 470px,rgba(235,232,228,.9),rgba(235,232,228,0) 75%),
    linear-gradient(90deg,#b9b9b6 0%,#dcdcd8 30%,#ececea 55%,#d8d3cc 75%,#cfc9c2 100%)}
.hero h1{position:absolute;left:130px;top:130px;font-family:'Poppins',sans-serif;font-weight:700;font-size:39px;line-height:53px;color:#111;text-transform:uppercase}
.btn{display:inline-block;background:var(--red);color:var(--white);font-family:'Poppins',sans-serif;text-transform:uppercase;text-decoration:none;white-space:nowrap}
.hero .btn{position:absolute;left:136px;top:253px;width:121px;height:40px;line-height:40px;text-align:center;font-size:14px;font-weight:600}
.dots{position:absolute;left:562px;top:517px;display:flex;gap:11px}
.dots span{width:7px;height:7px;border-radius:50%;background:#333}
.dots span.on{background:var(--red)}
.section-title{position:absolute;left:0;width:1200px;text-align:center;font-family:'Oswald',sans-serif;font-weight:400;font-size:28px;text-transform:uppercase;color:var(--ink)}
.card{position:absolute;background:var(--white);border:1px solid var(--line)}
.card .photo{width:100%;display:block}
.card .meta{font-size:10px;color:#333;margin:26px 0 0 23px}
.card h3{font-size:13px;font-weight:600;line-height:18px;margin:8px 16px 0 23px}
.card p{font-size:11px;line-height:16px;color:#333;margin:12px 14px 0 23px}
.card .btn{position:absolute;left:23px;bottom:27px;font-size:9px;font-weight:600;padding:0 11px;height:24px;line-height:24px}
.difference{top:1201px;left:0;width:1200px;height:516px;
  background:
    radial-gradient(ellipse 90px 130px at 690px 445px,rgba(245,170,40,.9),rgba(245,170,40,0) 70%),
    radial-gradient(ellipse 230px 280px at 690px 280px,rgba(70,60,70,.55),rgba(70,60,70,0) 75%),
    radial-gradient(ellipse 200px 300px at 1080px 260px,rgba(205,170,120,.8),rgba(205,170,120,0) 75%),
    linear-gradient(90deg,#5e4536 0%,#8f6a50 25%,#a88468 55%,#b99775 80%,#8b6b55 100%)}
.difference .panel{position:absolute;left:133px;top:58px;width:359px;height:402px;background:rgba(30,26,24,.9);padding:44px 34px 0 40px;color:var(--white)}
.difference h2{font-family:'Oswald',sans-serif;font-weight:400;font-size:28px;text-transform:uppercase;margin-bottom:12px}
.difference p{font-family:'IBM Plex Serif',serif;font-size:17px;line-height:24px;color:#eee}
.more{top:1717px;left:0;width:1200px;height:464px;background:var(--blush)}
.offer{position:absolute;top:120px;width:452px;height:293px;background:var(--white);box-shadow:0 2px 8px rgba(0,0,0,.08)}
.offer .label{position:absolute;left:40px;top:85px;font-family:'Oswald',sans-serif;font-size:29px;text-transform:uppercase;border-top:3px solid var(--red);border-bottom:2px solid var(--red);padding:8px 0 5px;white-space:nowrap}
.offer .label b{color:var(--red);font-weight:400}
.offer .label b.keep{text-transform:none}
.offer .cover{position:absolute}
.faq{top:2745px;left:0;width:1200px;height:399px;
  background:
    radial-gradient(ellipse 260px 200px at 600px 150px,rgba(120,95,75,.45),rgba(120,95,75,0) 75%),
    radial-gradient(ellipse 240px 200px at 1000px 120px,rgba(150,120,90,.35),rgba(150,120,90,0) 75%),
    linear-gradient(180deg,#211d1b,#3a302b 60%,#241f1c)}
.faq .section-title{color:var(--white);top:48px}
.faq-item{position:absolute;width:401px;height:53px;border:1px solid rgba(255,255,255,.85);color:var(--white);font-family:'Montserrat',sans-serif;font-size:14.5px;line-height:51px;padding-left:22px;white-space:nowrap}
.faq-item svg{position:absolute;right:14px;top:13px}
.quote{position:absolute;top:3265px;width:296px;height:281px;background:var(--white);box-shadow:0 2px 10px rgba(0,0,0,.09);text-align:center;font-family:'Inter',sans-serif}
.quote .mark{font-family:'IBM Plex Serif',serif;font-size:42px;font-weight:400;margin-top:28px;height:40px;line-height:40px}
.quote p{font-size:16px;line-height:25px;color:#333;margin:18px 40px 0}
.quote hr{width:36px;border:0;border-top:1px solid #bbb;margin:28px auto 22px}
.quote cite{font-style:normal;font-size:11.5px;line-height:17px;color:#444;display:block}
.site-footer{top:3608px;left:0;width:1200px;height:188px;background:#000}
.site-footer .nav a{color:var(--white)}
.copy{position:absolute;top:146px;left:0;width:1200px;text-align:center;color:var(--white);font-size:10.5px}
</style>
</head>
<body>

<header class="site-header abs">
  <div class="brand abs" style="left:133px;top:18px"><i></i>Pressing Hints</div>
  <nav class="nav">
    <a style="left:500px;top:30px">FREE LESSONS</a>
    <a style="left:640px;top:30px">THE DIFFERENCE</a>
    <a style="left:804px;top:30px">ARTICLES</a>
    <a style="left:916px;top:30px">CONTACT</a>
    <a style="left:1014px;top:30px">PRAISE</a>
  </nav>
</header>

<section class="hero abs" role="img" aria-label="Smiling woman drinking a glass of orange juice in a bright kitchen">
  <h1>Fresh and Blend Dishes<br>For Vigor</h1>
  <a class="btn">Read More</a>
  <div class="dots"><span></span><span></span><span class="on"></span><span></span><span></span></div>
</section>

<h2 class="section-title" style="top:679px">Receipes</h2>

<article class="card" style="left:119px;top:752px;width:231px;height:393px">
  <div class="photo" role="img" aria-label="Aloe vera plant" style="height:181px;background:radial-gradient(circle at 50% 55%,#8fb870,#3d6b33 55%,#1f3a1c)"></div>
  <div class="meta">March 15, 2015 by Rob Halden</div>
  <h3>Aloe Vera Juice &amp; Smoothie Recipes &amp; Benefits</h3>
  <p>Aloe vera juice is remarkably rich in nutrients that we are only beginning to understand.</p>
  <a class="btn">Read More</a>
</article>
<article class="card" style="left:362px;top:752px;width:231px;height:393px">
  <div class="photo" role="img" aria-label="Beet smoothie with apples and beets" style="height:181px;background:radial-gradient(circle at 62% 38%,#e0409a,#a02a5e 45%,#5f6b2e 80%)"></div>
  <div class="meta">March 15, 2015 by Rob Halden</div>
  <h3>Beet Juice &amp; Smoothie Recipes &amp; Benefits</h3>
  <p>Beet juice is low in fat and high in fiber. It's rich in phytonutrients, minerals, antioxidants...</p>
  <a class="btn">Read More</a>
</article>
<article class="card" style="left:605px;top:752px;width:231px;height:393px">
  <div class="photo" role="img" aria-label="Glasses of green, pink and orange juice" style="height:181px;background:linear-gradient(110deg,#9cc83a 0%,#e7d2c6 40%,#ea7a2a 70%,#8a1e14 100%)"></div>
  <div class="meta">March 15, 2015 by Rob Halden</div>
  <h3>Cabbage Juice &amp; Smoothie Recipes &amp; Benefits</h3>
  <p>Cabbage has been grown the world over for thousands of years, from Asia and southern Europe,</p>
  <a class="btn">Read More</a>
</article>
<article class="card" style="left:847px;top:752px;width:231px;height:393px">
  <div class="photo" role="img" aria-label="Carrot juice with fresh carrots" style="height:181px;background:radial-gradient(ellipse at 60% 60%,#ec6a1e,#f2a066 45%,#f1ebe3 80%)"></div>
  <div class="meta">March 15, 2015 by Rob Halden</div>
  <h3>Carrot Juice &amp; Smoothie Recipes &amp; Benefits</h3>
  <p>Archeologists have discovered carrot seeds dating to the Mesolithic period - as old as 20,000 years ago!</p>
  <a class="btn">Read More</a>
</article>

<section class="difference abs" role="img" aria-label="Happy woman holding a glass of orange juice in a rustic kitchen">
  <div class="panel">
    <h2>The Difference</h2>
    <p>If you have a health concern, these recipes heal. Yes, heal! I don't make a claim unless it's backed by science, and I cite the research so you can check it. Just as important, one glass of fresh juice is the easiest way to get all the fruits and veggies that nutritional science says we need. I juice instead of buying expensive multivitamins.</p>
  </div>
</section>

<section class="more abs">
  <h2 class="section-title" style="top:60px">More For You</h2>
  <div class="offer" style="left:133px">
    <div class="label"><b>Print</b> Version</div>
    <div class="cover" role="img" aria-label="Hardcover book, red cover" style="left:235px;top:22px;width:142px;height:238px;background:linear-gradient(160deg,#e0342a,#9a1a14);transform:rotate(14deg);box-shadow:8px 8px 12px rgba(0,0,0,.25)"></div>
  </div>
  <div class="offer" style="left:615px">
    <div class="label"><b class="keep">eBook</b> Version</div>
    <div class="cover" role="img" aria-label="eBook cover shown on a tablet" style="left:245px;top:27px;width:173px;height:239px;background:linear-gradient(160deg,#d8302a,#8e1812);border:7px solid #1a1a1a;border-radius:8px"></div>
  </div>
</section>

<h2 class="section-title" style="top:2222px">Tips</h2>

<article class="card" style="left:133px;top:2291px;width:301px;height:398px">
  <div class="photo" role="img" aria-label="Woman holding a glass of juice by a window" style="height:193px;background:linear-gradient(90deg,#f2efe9 0%,#e9ddd0 35%,#b86e4a 55%,#ece6df 80%,#c4724a 100%)"></div>
  <h3 style="margin-top:26px">The Amazing Benefits of<br>Juicing &amp; Blending</h3>
  <p>I began seriously juicing a couple of years ago. I wish I started decades ago, because I can't believe all the benefits of fresh juice,</p>
  <a class="btn">Read More</a>
</article>
<article class="card" style="left:451px;top:2291px;width:302px;height:398px">
  <div class="photo" role="img" aria-label="Woman with orange juice and oranges at a table" style="height:193px;background:linear-gradient(180deg,#9ccfd6 0%,#d9c9b6 45%,#f3ead9 75%,#f0a030 100%)"></div>
  <h3 style="margin-top:26px">Create Your Own Recipes for<br>Juicing &amp; Smoothies</h3>
  <p>Increasingly today, more and more people are turning to recipes for juicing and smoothies to boost their energy and overcome such prevalent health problems as heart disease,</p>
  <a class="btn">Read More</a>
</article>
<article class="card" style="left:769px;top:2291px;width:301px;height:398px">
  <div class="photo" role="img" aria-label="Woman drinking a green smoothie" style="height:193px;background:linear-gradient(90deg,#e6ece2 0%,#7aae4a 40%,#3b2a24 65%,#d9ddd6 100%)"></div>
  <h3 style="margin-top:26px">Coconut Juice &amp; Smoothie<br>Recipes &amp; Benefits</h3>
  <p>The modern coconut, which grows primarily in the Philippines, India and South America, dates to fossilized remains from between 35 to 55 million years ago (Eocene period)</p>
  <a class="btn">Read More</a>
</article>

<section class="faq abs" role="img" aria-label="Dim background of people enjoying juice">
  <h2 class="section-title">Frequently Asked Questions</h2>
  <div class="faq-item" style="left:189px;top:132px">Avoiding Dangers<svg width="26" height="26" viewBox="0 0 26 26"><circle cx="13" cy="13" r="12" fill="#fff"/><path d="M8 11l5 5 5-5" stroke="#222" stroke-width="2" fill="none"/></svg></div>
  <div class="faq-item" style="left:609px;top:132px">Juicing on a Budget<svg width="26" height="26" viewBox="0 0 26 26"><circle cx="13" cy="13" r="12" fill="#fff"/><path d="M8 11l5 5 5-5" stroke="#222" stroke-width="2" fill="none"/></svg></div>
  <div class="faq-item" style="left:189px;top:210px">Why Are Greens So Important<svg width="26" height="26" viewBox="0 0 26 26"><circle cx="13" cy="13" r="12" fill="#fff"/><path d="M8 11l5 5 5-5" stroke="#222" stroke-width="2" fill="none"/></svg></div>
  <div class="faq-item" style="left:609px;top:210px">Juicing on a Budget<svg width="26" height="26" viewBox="0 0 26 26"><circle cx="13" cy="13" r="12" fill="#fff"/><path d="M8 11l5 5 5-5" stroke="#222" stroke-width="2" fill="none"/></svg></div>
  <div class="faq-item" style="left:189px;top:290px">There are many variations of passages?<svg width="26" height="26" viewBox="0 0 26 26"><circle cx="13" cy="13" r="12" fill="#fff"/><path d="M8 11l5 5 5-5" stroke="#222" stroke-width="2" fill="none"/></svg></div>
  <div class="faq-item" style="left:609px;top:290px">Sed ut perspiciatis unde omnis iste natus?<svg width="26" height="26" viewBox="0 0 26 26"><circle cx="13" cy="13" r="12" fill="#fff"/><path d="M8 11l5 5 5-5" stroke="#222" stroke-width="2" fill="none"/></svg></div>
</section>

<h2 class="section-title" style="top:3189px">Praise</h2>
<svg class="abs" style="left:66px;top:3392px" width="16" height="26" viewBox="0 0 16 26"><path d="M13 2L3 13l10 11" stroke="#999" stroke-width="2" fill="none"/></svg>
<svg class="abs" style="left:1105px;top:3392px" width="16" height="26" viewBox="0 0 16 26"><path d="M3 2l10 11L3 24" stroke="#999" stroke-width="2" fill="none"/></svg>

<blockquote class="quote" style="left:133px">
  <div class="mark">“</div>
  <p>Thanks so much for putting out such a great - affordable - book</p>
  <hr>
  <cite>Dr. Lorena Whitfield,<br>Medical Director, Richmond, VA</cite>
</blockquote>
<blockquote class="quote" style="left:453px">
  <div class="mark">“</div>
  <p>I must say that this is a very well written and researched book. Thank you.</p>
  <hr>
  <cite>Dr. Marisol Teodoro<br>Manila, Philippines</cite>
</blockquote>
<blockquote class="quote" style="left:772px">
  <div class="mark">“</div>
  <p>I'm just getting started with the juicing habit and find your website very informative and easy to understand.</p>
  <cite style="margin-top:26px">Leilani, CA</cite>
</blockquote>

<footer class="site-footer abs">
  <div class="brand abs" style="left:136px;top:38px"><i></i>Pressing Hints</div>
  <nav class="nav">
    <a style="left:500px;top:54px">FREE LESSONS</a>
    <a style="left:640px;top:54px">THE DIFFERENCE</a>
    <a style="left:805px;top:54px">ARTICLES</a>
    <a style="left:916px;top:54px">CONTACT</a>
    <a style="left:1015px;top:54px">PRAISE</a>
  </nav>
  <div class="abs" style="left:133px;top:111px;width:938px;border-top:1px solid #333"></div>
  <div class="copy">Copyright © 2021 All Rights Reserved</div>
</footer>

</body>
</html>
```